Fashion Site

I need a Home Page and one Internal Page (About or Stores you choose) for a Fashion Retailer called VARELO based in Melbourne Australia. Their product range is high end - European brand (i.e. Velto, Darnex etc) shoes, handbags and accessories for Women and Men (Customers 75% Women 25% Men). They currently have a site at www.mirena-shop.com.au (My developer will take this design and push it through the rest of the site).

The new design will be clean and modern and reflect the high end brands they sell. The finished site will have the home page plus the following pages - About - Stores - News/Sales - E-Shop - Contact with links to Join our mail list - Chatterbook - Snapreel. I would like a main banner/slider at the top that will have 6 sliding images - through these images I would like to reinforce the following - the products are imported direct from Italy and are the latest most current designs from leading fashion houses (women and men) - A Modern Look with an Italian feel. Then we would also like to show some products/specials from the new E-Shop on the home page as well as the usual links etc.

Their colours are black and white but I am open to having a splash of colour and a must is to use the photography supplied in a creative way (see http://plumtorvel.com as an Idea), we want to show that the products are high end - hand made. Their end/tag line is Always In Fashion. We DO NOT want any brand names mentioned/Listed (if on a photo that is fine). The site will need to be easy to navigate and google friendly so please keep this in mind with the design. The images supplied include: Product Shots, Melbourne Stores, Italy Warehouse (2 story building with red roof) and Italy Factories/Craftsmen.

Target Market(s)

Fashion Conscious Women and Men who like the finer things in life

Industry/Entity Type

Fashion

Font styles to use
Serif
Sans Serif

Requirements
Must have
• Top Banner with 6 Images that Slide/Scroll in a banner.
Nice to have
• See the Following Sites that may inspire:
https://www.kivo.com.au
http://www.sundrapeq.co (the Look not the colours)
http://www.tolgaberry.com
Also Like the banner in this http://plumtorvel.com (Just the banner)

```html
<!DOCTYPE html>
<html lang="en">
<head>
<meta charset="utf-8">
<title>VARELO – Always In Fashion</title>
<link rel="stylesheet" href="https://fonts.googleapis.com/css2?family=Bebas+Neue&family=Arimo:wght@400&display=swap">
<style>
  :root {
    --page-bg: #fbfbfb;
    --ink: #1a1a1a;
    --nav-ink: #2b2b2b;
    --muted: #9a9a9a;
    --body-text: #4a4a4a;
    --black: #000000;
    --slate: #5a5a5a;
    --panel: #f2f2f2;
    --rule: #e6e6e6;
    --stripe: #dcdcdc;
    --footer: #f3f3f3;
    --white: #ffffff;
  }
  * { margin: 0; padding: 0; box-sizing: border-box; }
  html, body { width: 1143px; height: 1200px; overflow: hidden; }
  body {
    position: relative;
    background: var(--page-bg);
    font-family: "Arimo", Arial, sans-serif;
    color: var(--ink);
  }

  .top-rule {
    position: absolute; left: 0; top: 21px; width: 1143px; height: 5px;
    background: var(--rule);
  }
  .top-rule::after {
    content: ""; position: absolute; left: 490px; top: 5px;
    border-left: 6px solid transparent; border-right: 6px solid transparent;
    border-top: 6px solid var(--rule);
  }

  .brand {
    position: absolute; left: 188px; top: 48px;
    font-family: "Bebas Neue", sans-serif; font-size: 58px; line-height: 1;
    color: var(--ink); letter-spacing: 1px;
  }

  .main-nav { position: absolute; top: 62px; left: 0; }
  .nav-item { position: absolute; text-align: center; white-space: nowrap; }
  .nav-item .nav-hint {
    display: block; font-family: "Bebas Neue", sans-serif; font-size: 10.5px;
    color: var(--muted); letter-spacing: .3px;
  }
  .nav-item .nav-label {
    display: block; font-family: "Bebas Neue", sans-serif; font-size: 21px;
    color: var(--nav-ink); line-height: 1; margin-top: 2px;
  }

  .slider-top {
    position: absolute; left: 188px; top: 135px; width: 767px; height: 71px;
    background: var(--black);
  }
  .slider-photo {
    position: absolute; left: 188px; top: 208px; width: 767px; height: 317px;
    background: linear-gradient(180deg, #b9bcc4 0%, #a6a295 55%, #4a3b28 85%, #2d2419 100%);
  }
  .slider-bar {
    position: absolute; left: 188px; top: 528px; width: 767px; height: 59px;
    background: var(--black);
  }
  .slider-bar .bar-brand {
    position: absolute; left: 0; top: 0; width: 98px; height: 59px;
    background: var(--slate);
    font-family: "Bebas Neue", sans-serif; font-size: 24px; color: var(--ink);
    display: flex; align-items: center; justify-content: center;
  }
  .slide-dots { position: absolute; right: 13px; top: 36px; display: flex; gap: 6px; }
  .slide-dots span { width: 19px; height: 3px; background: var(--white); }
  .slide-dots span.is-current { background: var(--slate); }
  .slider-bar::after {
    content: ""; position: absolute; left: 386px; bottom: 0;
    border-left: 7px solid transparent; border-right: 7px solid transparent;
    border-bottom: 7px solid var(--panel);
  }

  .intro {
    position: absolute; left: 188px; top: 587px; width: 767px; height: 78px;
    background: var(--panel);
    padding: 39px 13px 0 13px;
    font-size: 10.5px; line-height: 12px; color: var(--body-text);
  }

  .section-head {
    position: absolute; left: 188px; top: 698px; width: 767px; height: 22px;
    background: repeating-linear-gradient(135deg, var(--stripe) 0 1px, transparent 1px 4px);
    border-top: 1px solid var(--rule); border-bottom: 1px solid var(--rule);
  }
  .section-head h2 {
    position: absolute; left: 50%; top: 1px; transform: translateX(-50%);
    padding: 0 12px; background: var(--page-bg);
    font-family: "Bebas Neue", sans-serif; font-weight: 400; font-size: 17px;
    color: var(--nav-ink); line-height: 20px; white-space: nowrap;
  }

  .product { position: absolute; top: 764px; width: 180px; }
  .product-photo {
    width: 180px; height: 97px;
    background: linear-gradient(90deg, #eef0f2 0%, #3f6fa8 30%, #3a66a0 55%, #d9574c 75%, #eceef0 100%);
  }
  .product h3 {
    margin: 19px 0 0 2px;
    font-family: "Bebas Neue", sans-serif; font-weight: 400; font-size: 15px;
    color: var(--nav-ink); line-height: 1;
  }
  .product p {
    margin-top: 6px; font-size: 10px; line-height: 15px; color: var(--body-text);
  }
  .product .view-link {
    display: flex; align-items: center; gap: 8px; margin: 6px 0 0 3px;
    font-family: "Bebas Neue", sans-serif; font-size: 12.5px; color: var(--nav-ink);
    text-decoration: none;
  }

  .site-footer {
    position: absolute; left: 0; top: 1088px; width: 1143px; height: 112px;
    background: var(--footer); border-top: 2px dotted var(--rule);
  }
  .site-footer p {
    position: absolute; left: 190px; top: 24px; font-size: 9.5px; color: var(--muted);
  }
  .site-footer strong { color: var(--nav-ink); font-weight: 400; }
</style>
</head>
<body>
  <div class="top-rule"></div>

  <header>
    <div class="brand">VARELO</div>
    <nav class="main-nav">
      <a class="nav-item" style="left:391px"><span class="nav-hint">Homepage</span><span class="nav-label">Home</span></a>
      <a class="nav-item" style="left:477px"><span class="nav-hint">Who are we?</span><span class="nav-label">About</span></a>
      <a class="nav-item" style="left:576px"><span class="nav-hint">Where to find us</span><span class="nav-label">Stores</span></a>
      <a class="nav-item" style="left:684px"><span class="nav-hint">Latest news</span><span class="nav-label">News/Sales</span></a>
      <a class="nav-item" style="left:804px"><span class="nav-hint">Where to buy</span><span class="nav-label">E-Shop</span></a>
      <a class="nav-item" style="left:893px"><span class="nav-hint">Get in touch</span><span class="nav-label">Contact</span></a>
    </nav>
  </header>

  <section class="slider">
    <div class="slider-top"></div>
    <div class="slider-photo" role="img" aria-label="Slide photo: two pairs of strappy sandals, cream and black, with gold metallic heels, shown from behind"></div>
    <div class="slider-bar">
      <div class="bar-brand">VARELO</div>
      <div class="slide-dots">
        <span class="is-current"></span><span></span><span></span><span></span><span></span><span></span>
      </div>
    </div>
  </section>

  <div class="intro">
    Lorem ipsum dolor sit amet, consectetur adipiscing elit. Vivamus non diam et lacus pulvinar venenatis et vestibulum velit. Pellentesque interdum faucibus dui hendrerit ultrices. Aliquam erat volutpat. Duis commodo turpis id diam pulvinar hendrerit.
  </div>

  <div class="section-head"><h2>Special Products This Month</h2></div>

  <article class="product" style="left:188px">
    <div class="product-photo" role="img" aria-label="Product photo: blue and red leather driving loafers"></div>
    <h3>Serrano Mens</h3>
    <p>Maecenas ipsum metus, semper hendrerit varius mattis, congue sit amet tellus. Aliquam ullamcorper dui sed magna posue re ut elementum enim rutrum.</p>
    <a class="view-link"><svg width="12" height="8" viewBox="0 0 12 8"><path d="M1 0l4 4-4 4M6 0l4 4-4 4" fill="none" stroke="#2b2b2b" stroke-width="2"/></svg>View Product</a>
  </article>
  <article class="product" style="left:384px">
    <div class="product-photo" role="img" aria-label="Product photo: blue and red leather driving loafers"></div>
    <h3>Serrano Mens</h3>
    <p>Maecenas ipsum metus, semper hendrerit varius mattis, congue sit amet tellus. Aliquam ullamcorper dui sed magna posue re ut elementum enim rutrum.</p>
    <a class="view-link"><svg width="12" height="8" viewBox="0 0 12 8"><path d="M1 0l4 4-4 4M6 0l4 4-4 4" fill="none" stroke="#2b2b2b" stroke-width="2"/></svg>View Product</a>
  </article>
  <article class="product" style="left:580px">
    <div class="product-photo" role="img" aria-label="Product photo: blue and red leather driving loafers"></div>
    <h3>Serrano Mens</h3>
    <p>Maecenas ipsum metus, semper hendrerit varius mattis, congue sit amet tellus. Aliquam ullamcorper dui sed magna posue re ut elementum enim rutrum.</p>
    <a class="view-link"><svg width="12" height="8" viewBox="0 0 12 8"><path d="M1 0l4 4-4 4M6 0l4 4-4 4" fill="none" stroke="#2b2b2b" stroke-width="2"/></svg>View Product</a>
  </article>
  <article class="product" style="left:775px">
    <div class="product-photo" role="img" aria-label="Product photo: blue and red leather driving loafers"></div>
    <h3>Serrano Mens</h3>
    <p>Maecenas ipsum metus, semper hendrerit varius mattis, congue sit amet tellus. Aliquam ullamcorper dui sed magna posue re ut elementum enim rutrum.</p>
    <a class="view-link"><svg width="12" height="8" viewBox="0 0 12 8"><path d="M1 0l4 4-4 4M6 0l4 4-4 4" fill="none" stroke="#2b2b2b" stroke-width="2"/></svg>View Product</a>
  </article>

  <footer class="site-footer">
    <p>All Content Copyright 2014- <strong>varelo</strong>. All Rights Reserved.</p>
  </footer>
</body>
</html>
```